Halvick Ledgers & Advisory Tri-Fold Brochure (8.5"x11")

I need a professional looking brochure for my bookkeeping business. I am looking for something professional yet casual (not too corporate looking). I have attached a sample brochure that will outline the areas and a copy of our logo. I'd like to stick with shades of blue. The final product should communicate professional and personal.

Target Market(s)

Small service businesses.

Industry/Entity Type

Business

Font styles to use
Sans Serif

Requirements
Must have
• Professional looking photos of people in areas where it asks for a picture.

```html
<!DOCTYPE html>
<html lang="en">
<head>
<meta charset="utf-8">
<title>Halvick Ledgers & Advisory — Tri-Fold Brochure</title>
<link href="https://fonts.googleapis.com/css2?family=Open+Sans:wght@400;600;700&display=swap" rel="stylesheet">
<style>
  :root {
    --page-bg: #e9edf1;
    --sky-light: #eaf6fd;
    --sky-mid: #bfe3f7;
    --sky-deep: #7cc4ec;
    --band-blue: #3b78c9;
    --heading-blue: #1f6fc4;
    --accent-blue: #2a8ad8;
    --text-dark: #3a4450;
    --icon-dark: #2f3a44;
    --white: #ffffff;
  }
  * { box-sizing: border-box; margin: 0; padding: 0; }
  html, body { width: 1200px; height: 982px; overflow: hidden; }
  body {
    background: var(--page-bg);
    font-family: "Open Sans", Arial, sans-serif;
    color: var(--text-dark);
  }
  .brochure {
    position: absolute;
    left: 60px; top: 73px;
    width: 1080px; height: 835px;
    display: flex;
    box-shadow: 0 10px 30px rgba(30, 60, 90, .18);
  }
  .panel {
    position: relative;
    width: 360px; height: 100%;
    overflow: hidden;
    background: linear-gradient(160deg, var(--sky-light) 0%, var(--sky-mid) 55%, var(--sky-deep) 100%);
  }
  .panel + .panel { border-left: 1px solid rgba(255,255,255,.6); }
  .panel-facets { position: absolute; inset: 0; width: 100%; height: 100%; }
  .photo { position: absolute; }

  /* Panel 1 — what we do */
  .photo-finance {
    left: 90px; top: 18px; width: 250px; height: 170px;
    background: linear-gradient(135deg, #3c7fc9 0%, #9fcdf0 45%, #e3eef7 100%);
  }
  .services-heading {
    position: absolute; left: 40px; top: 212px; width: 290px;
    color: var(--heading-blue); font-weight: 700; font-size: 17px;
    line-height: 1.2; text-transform: uppercase;
  }
  .services-lead {
    position: absolute; left: 40px; top: 262px;
    font-size: 15px; color: var(--text-dark);
  }
  .services-body {
    position: absolute; left: 40px; top: 292px; width: 290px;
    font-size: 13.5px; line-height: 1.5; text-align: justify;
  }
  .cta {
    position: absolute; left: 0; right: 0; top: 600px; bottom: 0;
    background: linear-gradient(180deg, rgba(160,214,245,.5), rgba(110,190,238,.75));
    text-align: center; padding-top: 36px;
  }
  .cta-rule { width: 180px; height: 1px; background: var(--heading-blue); margin: 0 auto 16px; }
  .cta-text { color: var(--heading-blue); font-size: 21px; font-weight: 600; line-height: 1.35; }

  /* Panel 2 — contact */
  .tagline-band {
    position: absolute; left: 0; right: 0; height: 34px;
    background: var(--band-blue); color: var(--white);
    font-weight: 600; font-size: 14px; line-height: 34px; padding-left: 18px;
  }
  .panel-contact .tagline-band { top: 28px; }
  .photo-meeting {
    left: 0; right: 0; top: 62px; height: 420px;
    background: radial-gradient(ellipse at 55% 45%, #f4f8fb 0%, #aac1d6 35%, #3d4e60 75%, #1f2a36 100%);
  }
  .contact-heading {
    position: absolute; left: 120px; top: 508px;
    color: var(--heading-blue); font-size: 26px; font-weight: 700;
  }
  .contact-rule { position: absolute; left: 120px; top: 552px; width: 200px; height: 1px; background: var(--heading-blue); }
  .contact-list { position: absolute; left: 40px; top: 572px; list-style: none; }
  .contact-item { display: flex; align-items: center; gap: 14px; height: 42px; font-size: 15px; color: var(--accent-blue); }
  .contact-icon { width: 30px; height: 30px; flex: none; }

  /* Panel 3 — cover */
  .brand { position: absolute; right: 28px; top: 80px; text-align: right; }
  .brand-name { display: flex; align-items: center; justify-content: flex-end; gap: 8px;
    color: var(--heading-blue); font-weight: 700; font-size: 15px; }
  .brand-mark { width: 16px; height: 16px; background: var(--heading-blue); }
  .brand-place { font-size: 12px; color: var(--text-dark); margin-top: 4px; }
  .panel-cover .tagline-band { top: 208px; }
  .photo-team {
    left: 30px; right: 0; top: 242px; height: 370px;
    background: linear-gradient(160deg, #e6eef5 0%, #a7bccd 40%, #4a5a6c 75%, #2c3846 100%);
  }
  .cover-headline {
    position: absolute; left: 40px; top: 648px; width: 290px;
    color: var(--white); font-weight: 700; font-size: 25px; line-height: 1.25;
  }
</style>
</head>
<body>
<main class="brochure">

  <section class="panel panel-services">
    <svg class="panel-facets" viewBox="0 0 360 835" preserveAspectRatio="none" aria-hidden="true">
      <polygon points="0,520 360,380 360,835 0,835" fill="#ffffff" opacity=".12"/>
      <polygon points="0,0 140,0 0,260" fill="#ffffff" opacity=".25"/>
    </svg>
    <div class="photo photo-finance" role="img" aria-label="Photo of a globe with financial charts, pen and calculator"></div>
    <h2 class="services-heading">Here to simplify the bookkeeping process</h2>
    <p class="services-lead">What we do:</p>
    <p class="services-body">Allow business owners to spend more time focusing on their core business by providing comprehensive bookkeeping and business consulting services. We provide the financial data and tools that allow businesses to maximize profitability and focus on growth and other areas of their business. We consider our business to be an extension of your business and look forward to the opportunity to exceed your expectations!</p>
    <div class="cta">
      <div class="cta-rule"></div>
      <p class="cta-text">Let's talk<br>Schedule a no-obligation<br>consultation today</p>
    </div>
  </section>

  <section class="panel panel-contact">
    <svg class="panel-facets" viewBox="0 0 360 835" preserveAspectRatio="none" aria-hidden="true">
      <polygon points="0,835 360,600 360,835" fill="#ffffff" opacity=".15"/>
    </svg>
    <div class="tagline-band">Trustworthy - Experienced - Reliable</div>
    <div class="photo photo-meeting" role="img" aria-label="Photo of business people shaking hands in a bright office"></div>
    <h2 class="contact-heading">Contact Us</h2>
    <div class="contact-rule"></div>
    <ul class="contact-list">
      <li class="contact-item">
        <svg class="contact-icon" viewBox="0 0 30 30" aria-hidden="true"><circle cx="15" cy="15" r="15" fill="var(--icon-dark)"/><path d="M10 8c1-1 2 0 3 2s0 2-1 3c1 2 2 3 4 4 1-1 1-2 3-1s3 2 2 3c-1 2-3 3-6 1s-6-5-7-8 1-3 2-4z" fill="#fff"/></svg>
        Phone: 484.555.0142
      </li>
      <li class="contact-item">
        <svg class="contact-icon" viewBox="0 0 30 30" aria-hidden="true"><circle cx="15" cy="15" r="15" fill="var(--icon-dark)"/><rect x="8" y="10" width="14" height="10" fill="none" stroke="#fff" stroke-width="1.6"/><path d="M8 10l7 6 7-6" fill="none" stroke="#fff" stroke-width="1.6"/></svg>
        Email: mara@halvickledgers.com
      </li>
      <li class="contact-item">
        <svg class="contact-icon" viewBox="0 0 30 30" aria-hidden="true"><circle cx="15" cy="15" r="15" fill="var(--icon-dark)"/><g fill="none" stroke="#fff" stroke-width="1.4"><circle cx="15" cy="15" r="7"/><ellipse cx="15" cy="15" rx="3" ry="7"/><path d="M8 15h14M9 11h12M9 19h12"/></g></svg>
        Web: www.halvickledgers.com
      </li>
    </ul>
  </section>

  <section class="panel panel-cover">
    <svg class="panel-facets" viewBox="0 0 360 835" preserveAspectRatio="none" aria-hidden="true">
      <polygon points="0,0 200,0 0,180" fill="#ffffff" opacity=".3"/>
      <polygon points="0,620 360,600 360,835 0,835" fill="#3a8ad8" opacity=".35"/>
    </svg>
    <div class="brand">
      <div class="brand-name"><span class="brand-mark"></span>Halvick Ledgers &amp; Advisory</div>
      <div class="brand-place">Cedar Valley, PA</div>
    </div>
    <div class="tagline-band">Trustworthy - Experienced - Reliable</div>
    <div class="photo photo-team" role="img" aria-label="Photo of business professionals reviewing documents together outside an office"></div>
    <h1 class="cover-headline">Expert bookkeeping services for small businesses</h1>
  </section>

</main>
</body>
</html>
```